Website for IT consulting Company

I need a website upgrade, the existing site content is ok, I would also like to add a testimonial page, the site should be something that is easy for us to update content. You use the content from www.kelvanbrook.com as an example. I will also post update logo and artwork. I also need a contact form with some type of validation or captcha.

I added Coded to the Project

Please omit Address maps

Target Market(s)

small business, service oriented companies. We provide IT Consulting, support and mangement

Industry/Entity Type

Information Technology

Coding

Number of Pages Required

1 page

Font styles to use
Serif
Sans Serif

Requirements
Must have
• Contain logo attached, and content from existing web site www.kelvanbrook.com.
• Also need to update content easily, and be movable to different platforms.
• There is a catch phrase
• "Let us worry about your technology…” “ so you don’t have to!”
• Should be included.
Nice to have
• Testimonial page, Project page where we can post new and past projects and pictures
Should not have
• none

```html
<!DOCTYPE html>
<html lang="en">
<head>
<meta charset="utf-8">
<title>Kelvanbrook – IT Solutions</title>
<link href="https://fonts.googleapis.com/css2?family=Montserrat:wght@400;600;700;800&family=Open+Sans:wght@400;600;700&display=swap" rel="stylesheet">
<style>
:root{
  --orange:#f7941d;
  --orange-dark:#e5811a;
  --ink:#333333;
  --muted:#777777;
  --charcoal:#2f3135;
  --slate:#4a4b4f;
  --paper:#ffffff;
  --mist:#f2f2f2;
}
*{box-sizing:border-box;margin:0;padding:0}
html,body{width:1200px;height:3828px;overflow:hidden}
body{position:relative;font-family:"Open Sans",Arial,sans-serif;color:var(--ink);background:var(--paper)}
.block{position:absolute;left:0;width:1200px}
h1,h2,h3,h4{font-family:"Montserrat",Arial,sans-serif}
.btn{display:inline-block;border:2px solid var(--orange);color:var(--orange);font:600 14px "Open Sans",sans-serif;padding:9px 22px;background:transparent}

/* top bar + header */
.topbar{top:0;height:36px;background:#1f2023;color:#bbb;font-size:12px;line-height:36px;padding-left:40px}
.hero{top:36px;height:564px;background:linear-gradient(100deg,#2c3440 0%,#55606c 45%,#8a949e 75%,#3b434d 100%)}
.header{position:absolute;top:0;left:0;width:1200px;height:100px;background:rgba(30,31,35,.85)}
.brand{position:absolute;left:40px;top:28px;display:flex;align-items:center;gap:12px}
.brand-mark{width:40px;height:40px;background:var(--orange)}
.brand-name{font:800 34px "Montserrat",sans-serif;color:var(--paper);letter-spacing:1px}
.phone{position:absolute;right:140px;top:34px;display:flex;align-items:center;gap:12px;color:var(--paper);font:700 22px "Open Sans",sans-serif}
.phone-icon{width:32px;height:32px;background:var(--orange);display:grid;place-items:center}
.menu{position:absolute;right:40px;top:28px;width:44px;height:44px;border-left:1px solid #666;padding:10px 0 0 14px}
.menu span{display:block;width:26px;height:3px;background:var(--orange);margin-bottom:6px}
.hero-copy{position:absolute;left:40px;top:220px;color:var(--paper)}
.hero-copy h1{font-size:38px;font-weight:700;line-height:1.2;text-transform:uppercase}
.hero-copy p{font:600 20px "Montserrat",sans-serif;margin-top:8px;text-transform:uppercase;letter-spacing:.5px}
.hero-copy .btn{margin-top:28px;border-color:var(--paper);color:var(--paper);background:var(--orange)}
.hero-photo{position:absolute;left:560px;top:100px;width:260px;height:464px;background:linear-gradient(180deg,rgba(255,255,255,.12),rgba(0,0,0,.2))}
.quick-form{position:absolute;left:820px;top:150px;width:340px;height:360px;background:rgba(25,26,30,.85);padding:18px 20px}
.quick-form h3{color:var(--paper);font-size:20px;font-weight:700;margin-bottom:14px}
.field{height:36px;background:#e9e9e9;margin-bottom:10px;font-size:13px;color:#888;padding:9px 12px}
.field.first{background:#fff}
.field.area{height:120px}
.submit{display:block;width:100%;height:38px;background:var(--orange);color:#fff;font:700 14px "Open Sans",sans-serif;text-align:center;line-height:38px}
.dots{position:absolute;top:530px;left:0;width:1200px;display:flex;justify-content:center;gap:10px}
.dots i{width:12px;height:12px;border-radius:50%;background:#ddd}
.dots i:first-child{background:var(--paper);border:2px solid var(--orange)}

/* services */
.services{top:600px;height:348px;display:flex;justify-content:space-between;padding:60px 40px 0}
.service{width:350px}
.service-head{display:flex;align-items:center;gap:12px;margin-bottom:14px}
.service-head h3{font-size:14px;font-weight:700;text-transform:uppercase}
.service p{font-size:14px;line-height:1.6;color:var(--muted)}
.more{display:inline-flex;align-items:center;gap:8px;margin-top:14px;font-size:14px;font-weight:600}
.more i{width:18px;height:18px;border:2px solid var(--orange);border-radius:50%}

/* welcome */
.welcome{top:948px;height:332px;background:var(--orange);color:var(--paper);text-align:center;padding:60px 80px}
.welcome h2{font-size:30px;font-weight:700;margin-bottom:20px}
.welcome p{font-size:15px;line-height:1.6}
.welcome .btn{margin-top:26px;border-color:var(--paper);color:var(--paper)}

/* support diagram */
.support{top:1300px;height:540px}

/* flexible */
.flexible{top:1860px;height:480px;background:var(--mist)}
.server-photo{position:absolute;left:40px;top:20px;width:540px;height:440px;background:linear-gradient(90deg,#2e3b4a,#6f8496 50%,#c7d1da)}
.flex-copy{position:absolute;left:610px;top:30px;width:550px}
.flex-copy h2{font-size:28px;font-weight:700;line-height:1.25;text-transform:uppercase;margin-bottom:14px}
.flex-copy p{font-size:16px;line-height:1.6;color:#555}
.flex-copy ul{list-style:none;display:flex;gap:60px;margin-top:20px;font-size:14px;font-weight:600;color:#666}
.flex-copy li:before{content:"› ";color:var(--orange)}
.flex-copy .btn{margin-top:18px}

/* catch phrase */
.catch{top:2400px;height:360px;background:var(--paper)}
.catch-photo{position:absolute;left:560px;top:0;width:640px;height:360px;background:linear-gradient(120deg,#9aa7b4,#dde3e8 50%,#6c7682)}
.catch svg{position:absolute;left:0;top:0}
.catch-line{position:absolute;left:40px;top:110px;width:500px;color:var(--paper);text-align:center;font:800 30px/1.35 "Montserrat",sans-serif;text-transform:uppercase}

/* testimonials */
.testimonials{top:2780px;height:480px;text-align:center}
.testimonials h2{font-size:30px;font-weight:700;letter-spacing:1px}
.rule{width:60px;height:3px;background:var(--orange);margin:12px auto 40px}
.quotes{display:flex;justify-content:space-around;padding:0 60px}
.quote{width:300px}
.avatar{width:180px;height:180px;border-radius:50%;margin:0 auto 20px;background:linear-gradient(160deg,#cfcfcf,#7b7b7b);border:4px solid #eee}
.quote h4{font-size:16px;font-weight:700}
.quote p{font-size:13px;line-height:1.6;color:var(--muted);margin-top:6px}
.quote .link{color:var(--orange)}
.quote .read{font-size:13px;margin-top:6px;display:inline-flex;gap:6px;align-items:center}
.quote .read i{width:14px;height:14px;border:2px solid var(--orange);border-radius:50%}

/* newsletter */
.newsletter{top:3280px;height:240px;background:var(--mist);text-align:center;padding-top:70px}
.newsletter h2{font-size:26px;font-weight:700;text-transform:uppercase}
.newsletter small{display:block;font-size:13px;color:var(--muted);text-transform:uppercase;letter-spacing:1px;margin-top:4px}
.signup{display:flex;justify-content:center;margin-top:24px}
.signup span{width:300px;height:30px;border-bottom:1px solid #ccc;font-size:13px;color:#aaa;text-align:left;padding-top:6px}
.signup b{width:100px;height:30px;background:var(--orange);color:#fff;font-size:13px;line-height:30px}

/* contact */
.contact{top:3520px;height:260px;background:var(--slate);color:var(--paper);text-align:center;padding-top:30px}
.contact h2{font-size:22px;font-weight:700;text-transform:uppercase}
.contact .rule{margin:10px auto 26px}
.contact-row{display:flex;justify-content:center;gap:120px}
.contact-item{display:flex;flex-direction:column;align-items:center;gap:12px;font-size:15px}
.ring{width:56px;height:56px;border-radius:50%;border:2px solid var(--paper);display:grid;place-items:center}
.socials{display:flex;justify-content:center;gap:14px;margin-top:22px}
.socials i{width:32px;height:32px;border-radius:50%;border:2px solid #bbb}
.footer{top:3780px;height:48px;background:var(--orange);color:var(--paper);text-align:center;font-size:14px;line-height:48px}
</style>
</head>
<body>

<div class="block topbar">123 Street, City Name, DC 12345</div>

<section class="block hero">
  <div class="hero-photo" role="img" aria-label="Hand touching a glowing digital interface"></div>
  <header class="header">
    <div class="brand"><span class="brand-mark"></span><span class="brand-name">KELVANBROOK</span></div>
    <div class="phone"><span class="phone-icon"><svg width="16" height="16" viewBox="0 0 24 24"><path fill="#fff" d="M6.6 10.8a15 15 0 0 0 6.6 6.6l2.2-2.2c.3-.3.7-.4 1-.2 1.1.4 2.3.6 3.6.6.6 0 1 .4 1 1V20c0 .6-.4 1-1 1A17 17 0 0 1 3 4c0-.6.4-1 1-1h3.5c.6 0 1 .4 1 1 0 1.3.2 2.5.6 3.6.1.3 0 .7-.2 1z"/></svg></span>123-4567-8910</div>
    <div class="menu"><span></span><span></span><span></span></div>
  </header>
  <div class="hero-copy">
    <h1>IT Solutions that work for<br>your business.</h1>
    <p>A full service technology company</p>
    <span class="btn">Read More</span>
  </div>
  <form class="quick-form">
    <h3>QUICK CONTACT HERE..</h3>
    <div class="field first">Your Name</div>
    <div class="field">Your Email</div>
    <div class="field">Subject</div>
    <div class="field area">Your Message...</div>
    <span class="submit">SUBMIT</span>
  </form>
  <div class="dots"><i></i><i></i><i></i><i></i></div>
</section>

<section class="block services">
  <article class="service">
    <div class="service-head"><svg width="40" height="40" viewBox="0 0 40 40"><circle cx="20" cy="20" r="9" fill="none" stroke="#f7941d" stroke-width="5"/><circle cx="20" cy="20" r="15" fill="none" stroke="#f7941d" stroke-width="4" stroke-dasharray="5 5"/></svg><h3>Managed IT Solutions</h3></div>
    <p>Our staff will design, service, administer and maintain your IT needs. We are well versed on all major operating systems and network appliances...</p>
    <span class="more">Read More <i></i></span>
  </article>
  <article class="service">
    <div class="service-head"><svg width="40" height="40" viewBox="0 0 40 40"><path d="M8 32 L24 16" stroke="#f7941d" stroke-width="5"/><circle cx="28" cy="12" r="8" fill="none" stroke="#f7941d" stroke-width="4"/></svg><h3>Remote Diagnostic &amp; Support</h3></div>
    <p>Do you need a quick solution to a technical problem? With our free remote assistance tool, a member of our support team can view your desktop and share control...</p>
    <span class="more">Read More <i></i></span>
  </article>
  <article class="service">
    <div class="service-head"><svg width="40" height="40" viewBox="0 0 40 40"><rect x="15" y="4" width="10" height="8" fill="#f7941d"/><rect x="4" y="28" width="10" height="8" fill="#f7941d"/><rect x="26" y="28" width="10" height="8" fill="#f7941d"/><path d="M20 12v8M9 28v-8h22v8" fill="none" stroke="#f7941d" stroke-width="3"/></svg><h3>IT Infrastructure Design</h3></div>
    <p>Do you have more than one site? Do you need remote access? We can design and implement LANs, WANs and VPNs. Make your...</p>
    <span class="more">Read More <i></i></span>
  </article>
</section>

<section class="block welcome">
  <h2>WELCOME TO KELVANBROOK</h2>
  <p>Outsourcing is subcontracting a process, such as product design or manufacturing, to a third-party company. The decision to outsource is often made in the interest of lowering firm costs, redirecting or conserving energy directed at the competencies of a particular business, or to make more efficient use of land, labor, capital, technology and resources. Outsourcing became part of the business lexicon during the 1980s.</p>
  <span class="btn">Read More</span>
</section>

<section class="block support">
  <svg width="1200" height="540" viewBox="0 0 1200 540" font-family="Open Sans, sans-serif">
    <g stroke="#bbb" stroke-width="1.5" fill="none">
      <path d="M310 160 H470 L520 210"/><path d="M600 80 V170"/><path d="M880 140 H730 L690 190"/>
      <path d="M360 300 H480"/><path d="M860 300 H720"/><path d="M300 420 H470 L520 380"/>
      <path d="M600 480 V410"/><path d="M900 430 H730 L690 390"/>
    </g>
    <circle cx="600" cy="290" r="118" fill="none" stroke="#3a3b3f" stroke-width="26" stroke-dasharray="170 15"/>
    <circle cx="600" cy="290" r="118" fill="none" stroke="#f7941d" stroke-width="26" stroke-dasharray="60 310" stroke-dashoffset="-40"/>
    <circle cx="600" cy="290" r="118" fill="none" stroke="#f7941d" stroke-width="26" stroke-dasharray="60 310" stroke-dashoffset="-400"/>
    <text x="600" y="292" text-anchor="middle" font-family="Montserrat, sans-serif" font-weight="800" font-size="26" fill="#333">IT SUPPORT</text>
    <text x="600" y="316" text-anchor="middle" font-size="14" fill="#666">SOLUTIONS</text>
    <g font-size="12" fill="#999">
      <rect x="585" y="30" width="30" height="24" fill="#f7941d"/>
      <text x="600" y="72" text-anchor="middle" fill="#f7941d" font-weight="700">NETWORK ADMINISTRATION</text>
      <text x="600" y="88" text-anchor="middle">Lorem ipsum dolor sit amet,</text>
      <text x="600" y="102" text-anchor="middle">consectetur adipiscing elit, sed</text>

      <rect x="180" y="110" width="24" height="22" fill="#444"/>
      <text x="150" y="154" fill="#333" font-weight="700">NETWORK SECURITY</text>
      <text x="150" y="170">Lorem ipsum dolor sit amet,</text>
      <text x="150" y="184">consectetur adipiscing elit, sed</text>

      <rect x="890" y="110" width="26" height="20" fill="#444"/>
      <text x="890" y="150" fill="#333" font-weight="700">DESKTOP SUPPORT</text>
      <text x="890" y="166">Lorem ipsum dolor sit amet,</text>
      <text x="890" y="180">consectetur adipiscing elit, sed</text>

      <rect x="220" y="250" width="24" height="22" fill="#f7941d"/>
      <text x="210" y="292" fill="#f7941d" font-weight="700">WEB DESIGN</text>
      <text x="210" y="308">Lorem ipsum dolor sit amet,</text>
      <text x="210" y="322">consectetur adipiscing elit, sed</text>

      <rect x="870" y="262" width="26" height="22" fill="#f7941d"/>
      <text x="870" y="302" fill="#f7941d" font-weight="700">NETWORK CABLING</text>
      <text x="870" y="318">Lorem ipsum dolor sit amet,</text>
      <text x="870" y="332">consectetur adipiscing elit, sed</text>

      <rect x="140" y="380" width="22" height="24" fill="#444"/>
      <text x="110" y="424" fill="#333" font-weight="700">TELECOMMUNICATIONS</text>
      <text x="110" y="440">Lorem ipsum dolor sit amet,</text>
      <text x="110" y="454">consectetur adipiscing elit, sed</text>

      <rect x="910" y="400" width="22" height="24" fill="#444"/>
      <text x="910" y="444" fill="#333" font-weight="700">ANTIVIRUS SOLUTIONS</text>
      <text x="910" y="460">Lorem ipsum dolor sit amet,</text>
      <text x="910" y="474">consectetur adipiscing elit, sed</text>

      <rect x="588" y="484" width="24" height="20" fill="#f7941d"/>
      <text x="600" y="520" text-anchor="middle" fill="#f7941d" font-weight="700">DISASTER RECOVERY</text>
      <text x="600" y="536" text-anchor="middle">Lorem ipsum dolor sit amet, consectetur</text>
    </g>
  </svg>
</section>

<section class="block flexible">
  <div class="server-photo" role="img" aria-label="Technician working in a server room"></div>
  <div class="flex-copy">
    <h2>Flexible solutions for your<br>business needs</h2>
    <p>Kelvanbrook is a technology solution provider based in Houston, Texas. Our goal is to make technology a non-issue for individuals and small to medium size businesses ranging from 5 to 150 users. Kelvanbrook has the experience, the tools, high-level technology solutions and training to power your business and your work force. We understand that all business's have one goal in common!</p>
    <ul><li>DISASTER RECOVERY</li><li>AUDIO/VIDEO MULTIMEDIA</li></ul>
    <span class="btn">Read More</span>
  </div>
</section>

<section class="block catch">
  <div class="catch-photo" role="img" aria-label="Business team meeting around a laptop"></div>
  <svg width="700" height="360" viewBox="0 0 700 360"><polygon points="0,0 660,0 560,360 0,360" fill="#f7941d"/><polygon points="660,0 690,0 590,360 560,360" fill="#fff"/></svg>
  <p class="catch-line">"Let us worry about your technology..."<br>" so you don't have to!"</p>
</section>

<section class="block testimonials">
  <h2>TESTIMONIAL</h2>
  <div class="rule"></div>
  <div class="quotes">
    <div class="quote"><div class="avatar" role="img" aria-label="Portrait of a client"></div><h4>NAME, DIRECTOR</h4><p>"Lorem ipsum dolor sit amet, consectetur adipiscing elit, sed do eiusmod tempor incididunt ut labore magna."</p><p class="link">Lorem ipsum dolor</p><span class="read">read more <i></i></span></div>
    <div class="quote"><div class="avatar" role="img" aria-label="Portrait of a client"></div><h4>NAME, DIRECTOR</h4><p>"Lorem ipsum dolor sit amet, consectetur adipiscing elit, sed do eiusmod tempor incididunt ut labore magna."</p><p class="link">Lorem ipsum dolor</p><span class="read">read more <i></i></span></div>
    <div class="quote"><div class="avatar" role="img" aria-label="Portrait of a client"></div><h4>NAME, DIRECTOR</h4><p>"Lorem ipsum dolor sit amet, consectetur adipiscing elit, sed do eiusmod tempor incididunt ut labore magna."</p><p class="link">Lorem ipsum dolor</p><span class="read">read more <i></i></span></div>
  </div>
</section>

<section class="block newsletter">
  <h2>Subscribe to our newsletter</h2>
  <small>to receive the latest news &amp; update</small>
  <div class="signup"><span>Email</span><b>SUBMIT</b></div>
</section>

<section class="block contact">
  <h2>Get in touch with us</h2>
  <div class="rule"></div>
  <div class="contact-row">
    <div class="contact-item"><span class="ring"><svg width="22" height="22" viewBox="0 0 24 24"><path fill="#fff" d="M12 2a7 7 0 0 0-7 7c0 5 7 13 7 13s7-8 7-13a7 7 0 0 0-7-7zm0 9.5A2.5 2.5 0 1 1 12 6.5a2.5 2.5 0 0 1 0 5z"/></svg></span>123 Street, City Name, DC 12345</div>
    <div class="contact-item"><span class="ring"><svg width="22" height="22" viewBox="0 0 24 24"><path fill="#fff" d="M6.6 10.8a15 15 0 0 0 6.6 6.6l2.2-2.2c.3-.3.7-.4 1-.2 1.1.4 2.3.6 3.6.6.6 0 1 .4 1 1V20c0 .6-.4 1-1 1A17 17 0 0 1 3 4c0-.6.4-1 1-1h3.5c.6 0 1 .4 1 1 0 1.3.2 2.5.6 3.6.1.3 0 .7-.2 1z"/></svg></span>1 234 567 890</div>
    <div class="contact-item"><span class="ring"><svg width="22" height="22" viewBox="0 0 24 24"><path fill="#fff" d="M3 5h18v14H3zm2 2v.5l7 5 7-5V7l-7 5z"/></svg></span>info@kelvanbrook.com</div>
  </div>
  <div class="socials"><i></i><i></i><i></i><i></i><i></i><i></i></div>
</section>

<footer class="block footer">Copyright © 2007 - Kelvanbrook Development Group, Inc. - All rights reserved.</footer>

</body>
</html>
```